SkyvornQ Business Cards and Stationary Design

Need a design for our business cards and stationary. I want to carry on the theme of the logo. I want the business cards to have a design on the back. I would like the business cards and the stationary to carry the same theme, design scheme, and branding

Target Market(s)

Airlines and Maintenance Facilities

Industry/Entity Type

Aviation

Contact Information for Business Card

Name
Position Title
Address: 4827 Trellis Hollow Road, Kestrel Bay, Halvern, 34951
Office Number
Mobile Number
Email
Website

Font styles to use
Serif
Sans Serif

Colors

Designer to choose colors to be used in the design.

```html
<!DOCTYPE html>
<html lang="en">
<head>
<meta charset="utf-8">
<title>SkyvornQ Business Card</title>
<link href="https://fonts.googleapis.com/css2?family=Montserrat:wght@400;600;700&display=swap" rel="stylesheet">
<style>
  :root {
    --backdrop: #262626;
    --sky: #2aa4e0;
    --sky-light: #3db3e6;
    --sky-deep: #1f93d4;
    --navy: #17284f;
    --navy-soft: #2d4a7a;
    --white: #ffffff;
    --white-dim: rgba(255,255,255,0.85);
  }
  * { margin: 0; padding: 0; box-sizing: border-box; }
  html, body { width: 1200px; height: 800px; overflow: hidden; }
  body {
    background: var(--backdrop);
    font-family: "Montserrat", Arial, sans-serif;
    color: var(--white);
    position: relative;
  }
  .card {
    position: absolute;
    left: 330px;
    width: 540px;
    height: 310px;
    border-radius: 14px;
    overflow: hidden;
    background: linear-gradient(135deg, var(--sky-light) 0%, var(--sky) 50%, var(--sky-deep) 100%);
  }
  .card--front { top: 60px; }
  .card--back { top: 420px; border-radius: 0; }

  .brand { display: flex; flex-direction: column; align-items: center; }
  .brand-circle {
    border: 5px solid var(--white);
    border-radius: 50%;
    flex: none;
  }
  .brand-name {
    font-weight: 700;
    letter-spacing: 0.12em;
    color: var(--white);
    white-space: nowrap;
  }

  .card--front .front-content {
    position: absolute; inset: 0;
    display: flex; flex-direction: column; align-items: center; justify-content: center;
  }
  .card--front .brand { gap: 16px; }
  .card--front .brand-circle { width: 72px; height: 72px; }
  .card--front .brand-name { font-size: 40px; }
  .front-web {
    font-size: 14px; font-weight: 600; letter-spacing: 0.03em;
    align-self: flex-end; margin-right: 120px; margin-top: 10px;
  }

  .back-brand {
    position: absolute; left: 40px; top: 118px;
    gap: 12px;
  }
  .card--back .brand-circle { width: 56px; height: 56px; border-width: 4px; }
  .card--back .brand-name { font-size: 24px; }

  .tab-top {
    position: absolute; left: 240px; top: 0;
    width: 38px; height: 70px;
    background: var(--navy-soft);
    border-radius: 0 0 19px 19px;
  }
  .icon-band {
    position: absolute; left: 280px; top: 118px;
    width: 40px; height: 192px;
    background: var(--navy);
    border-radius: 20px 20px 0 0;
  }
  .icon { position: absolute; left: 9px; width: 22px; height: 22px; }
  .icon--phone { top: 22px; }
  .icon--web { top: 78px; }
  .icon--pin { top: 140px; }

  .holder { position: absolute; left: 338px; top: 36px; }
  .holder-name { font-size: 22px; font-weight: 600; letter-spacing: 0.05em; white-space: nowrap; }
  .holder-title { font-size: 12px; color: var(--white-dim); margin-top: 2px; }

  .contact {
    position: absolute; left: 338px;
    font-size: 12px; line-height: 1.45; letter-spacing: 0.02em;
    white-space: nowrap;
  }
  .contact--phone { top: 140px; }
  .contact--web { top: 196px; }
  .contact--address { top: 254px; }
</style>
</head>
<body>

<section class="card card--front" aria-label="Business card front">
  <div class="front-content">
    <div class="brand">
      <span class="brand-circle"></span>
      <span class="brand-name">SKYVORNQ</span>
    </div>
    <p class="front-web">www.skyvornq.com</p>
  </div>
</section>

<section class="card card--back" aria-label="Business card back">
  <div class="brand back-brand">
    <span class="brand-circle"></span>
    <span class="brand-name">SKYVORNQ</span>
  </div>

  <div class="tab-top"></div>
  <div class="icon-band">
    <svg class="icon icon--phone" viewBox="0 0 24 24" aria-hidden="true">
      <path fill="#fff" d="M6.6 10.8a15.1 15.1 0 0 0 6.6 6.6l2.2-2.2a1 1 0 0 1 1-.25 11.4 11.4 0 0 0 3.6.57 1 1 0 0 1 1 1V20a1 1 0 0 1-1 1A17 17 0 0 1 3 4a1 1 0 0 1 1-1h3.5a1 1 0 0 1 1 1c0 1.25.2 2.46.57 3.6a1 1 0 0 1-.25 1z"/>
    </svg>
    <svg class="icon icon--web" viewBox="0 0 24 24" aria-hidden="true" fill="none" stroke="#fff" stroke-width="1.6">
      <circle cx="12" cy="12" r="9.5"/>
      <ellipse cx="12" cy="12" rx="4.2" ry="9.5"/>
      <line x1="2.5" y1="12" x2="21.5" y2="12"/>
      <line x1="4" y1="7" x2="20" y2="7"/>
      <line x1="4" y1="17" x2="20" y2="17"/>
    </svg>
    <svg class="icon icon--pin" viewBox="0 0 24 24" aria-hidden="true">
      <path fill="#fff" d="M12 2a7 7 0 0 0-7 7c0 5.2 7 13 7 13s7-7.8 7-13a7 7 0 0 0-7-7zm0 9.5A2.5 2.5 0 1 1 12 6.5a2.5 2.5 0 0 1 0 5z"/>
    </svg>
  </div>

  <div class="holder">
    <h1 class="holder-name">DANA CORVELL</h1>
    <p class="holder-title">CEO/ Founder</p>
  </div>

  <p class="contact contact--phone">(555) 318-4072<br>1-800-555-0147</p>
  <p class="contact contact--web">info@skyvornq.com<br>www.skyvornq.com</p>
  <p class="contact contact--address">4827 Trellis Hollow Road<br>Kestrel Bay, Halvern, 34951</p>
</section>

</body>
</html>
```